Harborline Renewal Business Card Design

Professional and clean design. The design colors should flow with the logo. Two-sided card with the website on the back which is:

www.HarborlineRenewal.example.

"Specializing in Water Damage Restoration"

On the front I need the name, email, phone, and logo.

Name: Darnell Quisby
Email: Darnell@HarborlineRenewal.example
Phone: 555-318-2046 for now

I only have the Preview and Thumbnail right now but should have the source files uploaded within a day or two.

Target Market(s)

Flood victims, home owners with water damage from busted pipes etc...

Industry/Entity Type

Business

Contact Information for Business Card

Name: Darnell Quisby

Font styles to use
Serif
Sans Serif

Requirements
Must have
• Business Card Details Info

```html
<!DOCTYPE html>
<html lang="en">
<head>
<meta charset="utf-8">
<title>Harborline Renewal – Business Card</title>
<link rel="stylesheet" href="https://fonts.googleapis.com/css2?family=Open+Sans:wght@400;600;700&display=swap">
<style>
  :root {
    --stage: #1c1c1c;
    --brand-blue: #2a9ad6;
    --brand-light: #5ec2ee;
    --paper: #ffffff;
    --ink-blue: #2a8fcf;
    --faint: rgba(255,255,255,0.12);
  }
  html, body {
    margin: 0;
    padding: 0;
    width: 1200px;
    height: 741px;
    overflow: hidden;
    background: var(--stage);
    font-family: "Open Sans", sans-serif;
  }
  .canvas {
    position: relative;
    width: 1200px;
    height: 741px;
  }
  .card {
    position: absolute;
    top: 236px;
    width: 495px;
    height: 282px;
    overflow: hidden;
  }
  .card--back { left: 86px; background: var(--brand-blue); color: var(--paper); }
  .card--front { left: 618px; background: var(--brand-blue); }

  /* Back side */
  .back-decor {
    position: absolute;
    left: 79px; top: 0;
    width: 330px; height: 330px;
    border-radius: 50%;
    background: var(--faint);
    top: -8px;
  }
  .mark {
    position: absolute;
    border-radius: 50%;
  }
  .card--back .mark {
    left: 213px; top: 56px; width: 70px; height: 70px;
    background: var(--paper);
  }
  .wordmark {
    position: absolute;
    left: 0; right: 0;
    text-align: center;
    font-weight: 600;
    white-space: nowrap;
  }
  .card--back .wordmark {
    top: 136px; font-size: 32px; color: var(--paper);
  }
  .tagline {
    position: absolute;
    font-size: 12.5px;
    white-space: nowrap;
  }
  .card--back .tagline {
    left: 0; right: 0; top: 190px; text-align: center; color: var(--paper);
  }
  .web-rule {
    position: absolute;
    top: 247px;
    height: 1px;
    background: var(--paper);
  }
  .web-rule--left { left: 0; width: 138px; }
  .web-rule--right { left: 359px; width: 136px; }
  .back-web {
    position: absolute;
    left: 0; right: 0; top: 238px;
    text-align: center;
    font-size: 12.5px;
  }

  /* Front side */
  .front-swoosh { position: absolute; inset: 0; }
  .card--front .mark {
    left: 101px; top: 24px; width: 64px; height: 64px;
    background: var(--brand-light);
  }
  .front-brand {
    position: absolute; left: 22px; width: 224px; text-align: center;
  }
  .card--front .wordmark {
    position: static; font-size: 25px; color: var(--ink-blue); margin-top: 98px;
  }
  .card--front .tagline {
    position: static; font-size: 10.5px; color: var(--ink-blue); margin-top: 4px;
  }
  .holder-name {
    position: absolute; left: 24px; top: 170px;
    margin: 0; font-size: 20px; font-weight: 700; color: var(--ink-blue);
  }
  .contact-list {
    position: absolute; left: 24px; top: 204px;
    margin: 0; padding: 0; list-style: none;
    font-size: 13.5px; color: var(--ink-blue); line-height: 18px;
  }
  .contact-list li { display: flex; align-items: center; gap: 5px; }
  .contact-icon { width: 14px; height: 14px; flex: none; }
</style>
</head>
<body>
<main class="canvas">

  <section class="card card--back" aria-label="Card back">
    <div class="back-decor" aria-hidden="true"></div>
    <div class="mark" aria-hidden="true"></div>
    <div class="wordmark">Harborline Renewal</div>
    <div class="tagline">Specializing in Water Damage Restoration</div>
    <span class="web-rule web-rule--left"></span>
    <span class="web-rule web-rule--right"></span>
    <div class="back-web">www.HarborlineRenewal.example</div>
  </section>

  <section class="card card--front" aria-label="Card front">
    <svg class="front-swoosh" viewBox="0 0 495 282" width="495" height="282" aria-hidden="true">
      <path d="M0,0 L148,0 C390,12 492,112 457,198 C433,252 392,272 362,282 L0,282 Z" fill="var(--brand-light)"/>
      <path d="M0,0 L172,0 C380,22 468,118 442,192 C422,244 380,268 348,282 L0,282 Z" fill="var(--paper)"/>
    </svg>
    <div class="mark" aria-hidden="true"></div>
    <div class="front-brand">
      <div class="wordmark">Harborline Renewal</div>
      <div class="tagline">Specializing in Water Damage Restoration</div>
    </div>
    <h2 class="holder-name">Darnell Quisby</h2>
    <ul class="contact-list">
      <li>
        <svg class="contact-icon" viewBox="0 0 14 14" aria-hidden="true">
          <rect width="14" height="14" fill="var(--brand-light)"/>
          <path d="M3,5 Q7,2 11,5 L10,6.5 L8.5,5.8 L5.5,5.8 L4,6.5 Z M4.5,7.5 L9.5,7.5 L10.5,11 L3.5,11 Z" fill="#fff"/>
        </svg>
        555-318-2046
      </li>
      <li>
        <svg class="contact-icon" viewBox="0 0 14 14" aria-hidden="true">
          <rect width="14" height="14" fill="var(--brand-light)"/>
          <rect x="2.5" y="4" width="9" height="6.5" fill="none" stroke="#fff" stroke-width="1"/>
          <path d="M2.5,4 L7,8 L11.5,4" fill="none" stroke="#fff" stroke-width="1"/>
        </svg>
        Darnell@HarborlineRenewal.example
      </li>
      <li>
        <svg class="contact-icon" viewBox="0 0 14 14" aria-hidden="true">
          <rect width="14" height="14" fill="var(--brand-light)"/>
          <circle cx="7" cy="7" r="4.5" fill="none" stroke="#fff" stroke-width="1"/>
          <ellipse cx="7" cy="7" rx="2" ry="4.5" fill="none" stroke="#fff" stroke-width="0.8"/>
          <path d="M2.5,7 H11.5" stroke="#fff" stroke-width="0.8"/>
        </svg>
        www.HarborlineRenewal.example
      </li>
    </ul>
  </section>

</main>
</body>
</html>
```